Law Firm Website

We are a small California based law firm specializing in business, corporate and litigation matters. We need to have our website redesigned. We are looking for a new and fresh look for our site, keeping in mind that we are a law firm.
What we don't want:
**the traditional "gavel" and "scales of justice" look
**anything too crazy
What we do want:
**sophisticated yet modern and fresh corporate look and feel
**samples of websites we really like:
http://www.tarnwellhope.example
http://www.marrowgate.example/
we also like:
http://www.fenwoodastley.example/
http://www.qz.example/
http://www.brenhollow.example/
http://www.pvdn.example
http://www.nqrlaw.example/
The content will be whatever is currently on our website (www.okabelawgroup.example). We will be selecting the winner based on originality and keeping the above requirements in mind. Please note that the photos that you use will be the ones that we will be using, so choose wisely because the photos will make a difference.
Target Market(s)
Corporate clients
Industry/Entity Type
Law Firm
Look and feel

```html
<!DOCTYPE html>
<html lang="en">
<head>
<meta charset="utf-8">
<title>Okabe Law Group, LLP</title>
<link href="https://fonts.googleapis.com/css2?family=Cinzel&family=Tinos:wght@400;700&family=Arimo:wght@400;700&display=swap" rel="stylesheet">
<style>
:root{
  --ink:#111;
  --black:#000;
  --white:#fff;
  --muted:#9a9a9a;
  --rule:#d6d6d6;
  --nav-grey:#999;
  --brand-blue:#2a86dd;
  --footer-text:#bbb;
  --field:#1c1c1c;
}
*{margin:0;padding:0;box-sizing:border-box}
html,body{width:961px;height:1200px;overflow:hidden;background:var(--white)}
.page{position:relative;width:961px;height:1200px;font-family:"Arimo",Arial,sans-serif;color:var(--ink)}
.abs{position:absolute}
.serif{font-family:"Tinos","Times New Roman",serif}
.top-line{left:0;top:0;width:961px;height:2px;background:var(--black)}
.client-login{left:735px;top:0;width:106px;height:18px;background:var(--black);color:var(--white);font-size:9.5px;border-radius:0 0 4px 4px;display:flex;align-items:center;justify-content:center;gap:6px}
.client-login i{width:11px;height:11px;border:1.5px solid var(--white);border-radius:50%}
.brand-mark{left:162px;top:32px;width:84px;height:85px;background:var(--brand-blue)}
.brand-name{left:120px;top:120px;font-size:19px;font-weight:700;color:var(--ink);white-space:nowrap}
.nav{left:436px;top:93px;width:405px;display:flex;justify-content:space-between;padding:0 12px 0 14px;font-size:11.5px;letter-spacing:.2px}
.nav a{color:var(--nav-grey);text-decoration:none}
.nav a.active{color:var(--ink)}
.nav-rule{left:436px;top:140px;width:405px;height:2px;background:#777}
.nav-active{left:436px;top:137px;width:80px;height:5px;background:var(--black)}
.hero{left:119px;top:168px;width:722px;height:306px;background:var(--black);box-shadow:0 14px 16px -8px rgba(0,0,0,.45)}
.hero-photo{position:absolute;right:0;top:0;width:380px;height:306px;background:radial-gradient(ellipse at 60% 45%,#4a4a4a 0%,#262626 45%,#000 78%)}
.hero-title{position:absolute;left:25px;top:90px;font-family:"Cinzel",serif;font-size:39px;color:var(--white);letter-spacing:1px}
.hero-sub{position:absolute;left:25px;top:143px;font-size:19.5px;color:var(--white)}
.hero-btn{position:absolute;left:25px;top:175px;width:159px;height:34px;border:1.5px solid var(--white);color:var(--white);font-size:14px;display:flex;align-items:center;justify-content:center;letter-spacing:.5px}
.dots{position:absolute;left:340px;top:282px;display:flex;gap:5px}
.dots span{width:9px;height:9px;border-radius:50%;background:var(--white)}
.dots span.on{background:var(--black);border:2px solid var(--white)}
.practice{top:524px;width:215px;text-align:center}
.practice h2{font-size:18.5px;font-weight:400;letter-spacing:.3px}
.practice p{margin-top:10px;font-size:10px;line-height:15px;color:var(--muted)}
.read{font-family:"Tinos","Times New Roman",serif;font-size:10.5px;font-weight:700;color:var(--ink);letter-spacing:.2px}
.practice .read{display:block;margin-top:9px}
.divider{top:653px;height:1px;background:var(--rule)}
.section-title{font-size:20.5px;font-weight:400;letter-spacing:.2px}
.frame{background:var(--white);border:1px solid #ddd;box-shadow:0 1px 3px rgba(0,0,0,.15);padding:5px}
.frame div{width:100%;height:100%}
.welcome-text{left:120px;top:848px;width:362px;font-size:10px;line-height:15px;color:var(--muted);letter-spacing:.1px}
.help-item h3{font-size:12px;font-weight:400;color:var(--ink)}
.help-item p{margin-top:5px;font-size:10px;line-height:15px;color:var(--muted);width:215px}
.help-item .read{display:block;margin-top:4px}
.footer{left:0;top:965px;width:961px;height:235px;background:var(--black);color:var(--footer-text)}
.footer h2{position:absolute;color:var(--white);font-size:19px;font-weight:400;letter-spacing:.3px}
.topics{position:absolute;top:71px;font-size:10px;line-height:24px;list-style:none}
.topics li{position:relative;padding-left:22px}
.topics li::before{content:"";position:absolute;left:1px;top:9px;width:4px;height:4px;border-right:1.5px solid var(--footer-text);border-top:1.5px solid var(--footer-text);transform:rotate(45deg)}
.news{position:absolute;left:642px;top:69px;width:200px;font-size:9.5px;line-height:13px;letter-spacing:.2px}
.email{position:absolute;left:642px;top:106px;width:200px;height:25px;background:var(--field);font-size:10px;color:#aaa;padding:7px 9px}
.subscribe{position:absolute;left:642px;top:144px;width:71px;height:21px;border:1px solid #555;background:#222;color:var(--white);font-family:"Tinos","Times New Roman",serif;font-size:10px;display:flex;align-items:center;justify-content:center}
.foot-rule{position:absolute;left:119px;top:193px;width:722px;height:1px;background:#333}
.copyright{position:absolute;left:120px;top:208px;font-size:9.5px}
.copyright b{font-weight:400;color:var(--white)}
.social{position:absolute;left:764px;top:210px;display:flex;gap:13px}
.social span{width:9px;height:9px;border-radius:50%;background:var(--white)}
</style>
</head>
<body>
<div class="page">
  <div class="abs top-line"></div>
  <div class="abs client-login"><i></i>Client Login</div>

  <div class="abs brand-mark"></div>
  <div class="abs brand-name">Okabe Law Group, LLP</div>

  <nav class="abs nav serif">
    <a class="active" href="#">ABOUT US</a>
    <a href="#">INDIVIDUAL</a>
    <a href="#">CORPORATE</a>
    <a href="#">CONTACT US</a>
  </nav>
  <div class="abs nav-rule"></div>
  <div class="abs nav-active"></div>

  <section class="abs hero">
    <div class="hero-photo" role="img" aria-label="Three attorneys in dark suits and robes standing together"></div>
    <div class="hero-title">LOREM IPSUM</div>
    <div class="hero-sub serif">Donec at Etiam fermentum dictum</div>
    <div class="hero-btn serif">LEARN MORE</div>
    <div class="dots"><span></span><span></span><span class="on"></span><span></span></div>
  </section>

  <div class="abs practice serif" style="left:118px">
    <h2>CONTRACT LAW</h2>
    <p style="font-family:Arimo,Arial,sans-serif">Lorem ipsum dolor sit amet, consectetur adipiswing elit, sed do eiusmod temporum incididunt aliqua. Ut enim ad minim veniam.</p>
    <span class="read">READ MORE</span>
  </div>
  <div class="abs practice serif" style="left:372px">
    <h2>PROPERTY LAW</h2>
    <p style="font-family:Arimo,Arial,sans-serif">Lorem ipsum dolor sit amet, consectetur adipiswing elit, sed do eiusmod temporum incididunt aliqua. Ut enim ad minim veniam.</p>
    <span class="read">READ MORE</span>
  </div>
  <div class="abs practice serif" style="left:626px">
    <h2>CRIMINAL LAW</h2>
    <p style="font-family:Arimo,Arial,sans-serif">Lorem ipsum dolor sit amet, consectetur adipiswing elit, sed do eiusmod temporum incididunt aliqua. Ut enim ad minim veniam.</p>
    <span class="read">READ MORE</span>
  </div>

  <div class="abs divider" style="left:119px;width:347px"></div>
  <svg class="abs" style="left:472px;top:647px" width="16" height="12" viewBox="0 0 16 12" aria-hidden="true">
    <path d="M2 8 C4 2,7 2,8 6 C9 10,12 10,14 4" fill="none" stroke="#666" stroke-width="1.2"/>
  </svg>
  <div class="abs divider" style="left:496px;width:345px"></div>

  <h2 class="abs section-title serif" style="left:120px;top:687px">WELCOME TO LAW CENTRE!</h2>
  <div class="abs frame" style="left:119px;top:727px;width:361px;height:105px">
    <div role="img" aria-label="Business team reviewing documents at a laptop" style="background:linear-gradient(90deg,#2c3a4c 0%,#6f7f90 35%,#c9b49a 70%,#e9e4de 100%)"></div>
  </div>
  <p class="abs welcome-text">Lorem ipsum dolore concectetuor.<br>Lorem ipsum dolor sit amet, consectetur adipisicing elit, sed do eiuss mod tempor incididunt ut labore et dolore magna aliqua. Ut enim adu minim veniam, quis nostrud dolor in reprehenderit ...</p>
  <span class="abs read" style="left:120px;top:912px">READ MORE</span>

  <h2 class="abs section-title serif" style="left:537px;top:687px">NEED PRACTICAL HELP?</h2>

  <div class="abs frame" style="left:537px;top:728px;width:75px;height:75px">
    <div role="img" aria-label="Portrait of a smiling female attorney" style="background:linear-gradient(180deg,#cfd3d4,#a89a8c)"></div>
  </div>
  <div class="abs help-item" style="left:627px;top:727px">
    <h3 class="serif">MASSA AS LAOREETUM</h3>
    <p>Lorem ipsum dolor sit amet, consectetur adipiswing elit, sed do eiusmod temporum incididunt ut laboret dolore magna aliqua. Ut enim ad minim veniam.</p>
    <span class="read">READ MORE</span>
  </div>
  <div class="abs divider" style="left:537px;top:824px;width:304px"></div>

  <div class="abs frame" style="left:537px;top:847px;width:75px;height:75px">
    <div role="img" aria-label="Portrait of a male attorney in a dark suit" style="background:linear-gradient(180deg,#eceeef,#55585c)"></div>
  </div>
  <div class="abs help-item" style="left:627px;top:846px">
    <h3 class="serif">MASSA AS LAOREETUM</h3>
    <p>Lorem ipsum dolor sit amet, consectetur adipiswing elit, sed do eiusmod temporum incididunt ut laboret dolore magna aliqua. Ut enim ad minim veniam.</p>
    <span class="read">READ MORE</span>
  </div>

  <footer class="abs footer">
    <h2 class="serif" style="left:120px;top:26px">LEGAL TOPICS</h2>
    <ul class="topics" style="left:120px"><li>Auto Accidents</li><li>Bankruptcy</li><li>Business Law</li><li>Child Custody</li></ul>
    <ul class="topics" style="left:293px"><li>Child Support</li><li>Civil Rights</li><li>Consumer</li><li>Criminal Law</li></ul>
    <ul class="topics" style="left:458px"><li>Discrimination</li><li>Divorce</li><li>Drunk Driving</li><li>Education</li></ul>

    <h2 class="serif" style="left:642px;top:26px">LEGAL TOPICS</h2>
    <p class="news">Get OL Digest, our monthly newsletter, delivered to your inbox each month.</p>
    <div class="email">Your Email</div>
    <div class="subscribe">SUBSCRIBE</div>

    <div class="foot-rule"></div>
    <p class="copyright">Copyright © 2014, <b>LAW CENTRE</b>. All rights reserved.</p>
    <div class="social" aria-label="Social links"><span></span><span></span><span></span><span></span></div>
  </footer>
</div>
</body>
</html>
```